Creative, fresh business card design for Ripplecraft Facades

We need a fresh, creative business card design for Ripplecraft Facades. We are the manufacturer of Ripplecraft Facades in Australia. Wall panels are 2400 x 1200mm panels made from MDF and feature 3D patterns on the face of the panel. The colours to be used are green, silver/grey and white RGB
Red 187
Green 207
Blue 65.

An idea is to possibly use a watermark of one of our designs as a background (like on the "Grids" design on the left hand side of page 2 of our brochure).

Target Market(s)

Interior designers, architects, builders and home renovators

Industry/Entity Type

Business

Contact Information for Business Card

Details to go on the card are:
Our logo (attached),
Slogan: "Decorative panels for interiors and exteriors",
Contact name,
Position,
Mobile phone number,
Business address,
Business phone,
Business fax,
Website and
Email address.

I have attached a few images of our panels and our brochure for reference.

The colours of the business card should feature our logo colours which are: RGB
Red 187
Green 207
Blue 65

Requirements
Must have
• Very modern fonts and design. Some of the designs shown especially the "Prisms" design which is a popular design.
Nice to have
• Creative but simple design. Very contemporary.
Should not have
• Anything ornate or old fashioned.

```html
<!DOCTYPE html>
<html lang="en">
<head>
<meta charset="utf-8">
<title>Ripplecraft Facades – Business Card</title>
<link href="https://fonts.googleapis.com/css2?family=Lato:wght@400;700&display=swap" rel="stylesheet">
<style>
  :root {
    --brand-green: #bbcf41;
    --silver: #8e8e91;
    --ink: #3c3c3c;
    --card-white: #ffffff;
    --panel-grey: #5b5b5b;
    --backdrop: #000000;
  }
  * { margin: 0; padding: 0; box-sizing: border-box; }
  html, body {
    width: 1200px; height: 900px; overflow: hidden;
    background: var(--backdrop);
    font-family: "Lato", Arial, sans-serif;
  }
  .canvas { position: relative; width: 1200px; height: 900px; }

  .card {
    position: absolute; top: 192px;
    width: 303px; height: 491px;
    border-radius: 16px; overflow: hidden;
  }
  .card--front { left: 294px; background: var(--card-white); }
  .card--back { left: 622px; }

  .panel-texture {
    position: absolute; inset: 0;
    background:
      linear-gradient(135deg, #676767 0%, #545454 35%, #5e5e5e 60%, #4d4d4d 100%);
  }

  .brand-mark {
    position: absolute; width: 58px; height: 58px;
    background: var(--brand-green);
  }
  .card--front .brand-mark { left: 136px; top: 52px; }
  .card--back .brand-mark { left: 122px; top: 168px; }

  .brand-name {
    position: absolute; left: 0; width: 100%;
    text-align: center; font-weight: 700; font-size: 23px;
    letter-spacing: 0.2px; white-space: nowrap;
  }
  .card--front .brand-name { top: 126px; color: var(--silver); }
  .card--back .brand-name { top: 244px; color: var(--card-white); }

  .tagline {
    position: absolute; left: 0; width: 100%;
    text-align: center; font-size: 14px; line-height: 17px;
    letter-spacing: 1.9px; font-weight: 400;
  }
  .card--front .tagline { top: 182px; color: var(--silver); }
  .card--back .tagline { top: 299px; color: var(--card-white); font-size: 15px; line-height: 18px; letter-spacing: 2px; }

  .person { position: absolute; left: 37px; top: 240px; }
  .person__name { color: var(--brand-green); font-weight: 700; font-size: 28px; line-height: 32px; }
  .person__role { color: var(--ink); font-size: 15px; line-height: 18px; margin-top: 1px; }

  .contacts { position: absolute; left: 37px; top: 304px; list-style: none; }
  .contacts li {
    display: flex; align-items: center;
    height: 20.3px; font-size: 13px; color: var(--ink);
  }
  .contacts svg { width: 11px; height: 11px; margin-right: 8px; fill: var(--brand-green); flex: none; }

  .address {
    position: absolute; left: 37px; top: 413px;
    font-size: 13px; line-height: 17px; color: var(--ink);
  }
</style>
</head>
<body>
<main class="canvas">

  <section class="card card--front" aria-label="Card front">
    <div class="brand-mark"></div>
    <div class="brand-name">Ripplecraft Facades</div>
    <p class="tagline">decorative panels for<br>interiors &amp; landscapes</p>

    <div class="person">
      <h1 class="person__name">Liam Archer</h1>
      <p class="person__role">Director</p>
    </div>

    <ul class="contacts">
      <li><svg viewBox="0 0 12 12"><path d="M3 0h6v12H3z M4 1.5v8h4v-8z"/></svg>712-5550-184</li>
      <li><svg viewBox="0 0 12 12"><path d="M1 4c0-2 2-3 5-3s5 1 5 3v1H8V3.5H4V5H1z M2 6h8l1 5H1z"/></svg>717-(555)-026</li>
      <li><svg viewBox="0 0 12 12"><path d="M3 0h6v3H3z M1 4h10v7H1z M3 6v1h6V6z"/></svg>717-(555)-027</li>
      <li><svg viewBox="0 0 12 12"><path d="M0 2h12v8H0z M1 3l5 3.5L11 3v-.2H1z" fill-rule="evenodd"/></svg>info@ripplecraft.com</li>
      <li><svg viewBox="0 0 12 12"><circle cx="6" cy="6" r="5.5"/></svg>www.ripplecraftfacades.com</li>
    </ul>

    <p class="address">14 Kiln Street,<br>Marrickville NSW 2204</p>
  </section>

  <section class="card card--back" aria-label="Card back">
    <div class="panel-texture" role="img" aria-label="Faint grey prism wall panel pattern"></div>
    <div class="brand-mark"></div>
    <div class="brand-name">Ripplecraft Facades</div>
    <p class="tagline">decorative panels for<br>interiors &amp; landscapes</p>
  </section>

</main>
</body>
</html>
```